DeskHarbor - Coworking website design

DeskHarbor is a new global coworking brand, growing fast and establishing stylish locations and communities that inspire innovation and collaboration all around the world.
The project includes a complete website design, focused on delivering the company’s values and messages, provide information to site visitors and to generate leads.

Please review the attached design brief, for more information.

Target Market(s)

Both men and women. Decision makers in:
Small & medium businesses in various fields, but mainly technology firms (Startups or established brands).
Global enterprises.
Dynamic “new generation” companies.
Press

Number of Pages Required

2 page

Requirements
Must have
• Project Scope & deliverables:
• Concept and design for :
• Home page
• Deliver the values mentioned above.
• Showcase the cities in which the company has locations in.
• Show customer testimonials.
• Provide an interface (form) for booking a tour and/or leaving contact details for more information (two alternatives)
• Coworking location page - Each location is in the coolest part of a different major city, and has its own address, set of amenities (kitchen, fast internet etc,), area information (public transportation accessibility, sites near by, bars and restaurants in walking distance) and pricing for private offices (based on number of people per office). Each location page must have an interface to book a location tour.
• Site Navigation (header & footer) - allow simple navigation between multiple city pages, location pages and homepage. Growth of up to 50 locations in 25 cities.
• The navigation should account for Navigation to additional pages (not commissioned in this project) such as:
• Locations
• Enterprise
• Special promotions
• Blog
• Contact us
• About us
• Note - the site should account for geolocation variable display, showing different content for different locations.
• Deliverables must include all editable graphic files (photoshop or similar), as follows:
• Home page - Desktop view (preferably both)
• Location page - Mobile web view (preferably both)
• Navigation - both options

```html
<!DOCTYPE html>
<html lang="en">
<head>
<meta charset="utf-8">
<title>DeskHarbor — Coworking</title>
<link href="https://fonts.googleapis.com/css2?family=Roboto:ital,wght@0,300;0,400;0,500;0,700;1,400&display=swap" rel="stylesheet">
<style>
:root{
  --blue:#2e9fd9;
  --blue-dark:#1f86bf;
  --ink:#222;
  --text:#555;
  --muted:#888;
  --line:#cfcfcf;
  --white:#fff;
  --star:#f2b500;
}
*{box-sizing:border-box;margin:0;padding:0}
html,body{width:1200px;height:3396px;overflow:hidden}
body{position:relative;background:var(--white);font-family:'Roboto',sans-serif;color:var(--text)}
.abs{position:absolute}

/* Hero */
.hero{position:absolute;left:0;top:0;width:1200px;height:596px;background:linear-gradient(120deg,#6d6f70 0%,#9a9c9c 35%,#b8b7b2 60%,#7d7f80 100%)}
.hero-shade{position:absolute;inset:0;background:linear-gradient(90deg,rgba(0,0,0,.45),rgba(0,0,0,.05) 70%)}
.brand{position:absolute;left:97px;top:40px;display:flex;align-items:center;gap:14px;color:var(--white);font-size:28px;font-weight:500}
.brand-mark{width:34px;height:34px;border:3px solid currentColor}
.nav{position:absolute;top:45px;right:102px;display:flex;gap:30px;font-size:15px;font-weight:500;color:var(--white);align-items:center}
.hero-title{position:absolute;left:97px;top:194px;font-size:58px;font-weight:700;color:var(--white)}
.hero-sub{position:absolute;left:97px;top:274px;font-size:24px;color:var(--white);font-weight:400}
.btn-ghost{position:absolute;left:97px;top:336px;width:180px;height:45px;border:2px solid var(--white);border-radius:23px;color:var(--white);font-size:14px;font-weight:500;display:flex;align-items:center;justify-content:center}
.dots{position:absolute;left:567px;top:498px;display:flex;gap:6px}
.dots i{width:12px;height:12px;border-radius:50%;border:2px solid var(--white)}
.dots i:first-child{background:var(--white)}

/* Values */
.section-title{position:absolute;left:0;width:1200px;text-align:center;font-size:30px;font-weight:500;color:var(--ink)}
.intro{position:absolute;left:260px;width:680px;text-align:center;font-size:14px;line-height:27px;color:var(--muted)}
.value-card{position:absolute;top:865px;width:236px;height:226px;border:1px solid var(--line);text-align:center;padding-top:60px}
.value-card h3{font-size:18px;font-weight:500;color:var(--ink);line-height:28px}
.value-card p{font-size:13px;line-height:23px;color:var(--text);margin:12px 22px 0}
.value-card .more{display:block;margin-top:14px;font-size:12px;font-weight:700;color:var(--ink)}
.value-card.active{border-color:var(--blue)}
.value-card.active h3,.value-card.active .more{color:var(--blue)}
.value-icon{position:absolute;top:-50px;left:70px;width:96px;height:96px;border-radius:50%;background:var(--white);border:1px solid var(--line);display:flex;align-items:center;justify-content:center}
.value-card.active .value-icon{border-color:var(--blue)}
.chev{position:absolute;top:962px}

/* Testimonials */
.testimonials{position:absolute;left:0;top:1177px;width:1200px;height:390px;background:linear-gradient(90deg,rgba(46,159,217,.93),rgba(52,165,222,.88) 50%,rgba(46,159,217,.93)),linear-gradient(120deg,#4f6a7a,#8ea6b3);}
.testimonials .section-title{color:var(--white);top:70px}
.quote{position:absolute;top:140px;color:var(--white)}
.avatar{position:absolute;top:0;width:74px;height:74px;border-radius:50%;border:3px solid var(--white);background:radial-gradient(circle at 50% 45%,#c8b3a2,#8b7467)}
.quote-body{position:absolute;top:8px;width:226px;font-size:13px;font-style:italic;line-height:22px;color:#e8f5fc}
.quote-body b{font-size:22px;font-style:normal;margin-right:8px;vertical-align:-4px}
.quote-name{position:absolute;top:128px;font-size:11px;font-weight:500;text-transform:uppercase;white-space:nowrap}
.quote-role{position:absolute;top:146px;font-size:10px;font-style:italic;color:#dff1fb;white-space:nowrap}
.stars{position:absolute;top:170px;display:flex;gap:3px}
.arrow-round{position:absolute;top:200px;width:32px;height:32px;border-radius:50%;border:1px solid rgba(255,255,255,.7);display:flex;align-items:center;justify-content:center}

/* What we do */
.what{position:absolute;left:100px;top:1646px;width:1003px;height:398px;border:1px solid var(--line)}
.what-media{position:absolute;left:0;top:4px;width:464px;height:390px;background:linear-gradient(135deg,#5b4d42,#a88e75 45%,#d8d0c4 70%,#6f6a66)}
.play{position:absolute;left:204px;top:166px;width:56px;height:56px;border-radius:50%;background:rgba(0,0,0,.75);display:flex;align-items:center;justify-content:center}
.what h2{position:absolute;left:502px;top:46px;font-size:28px;font-weight:500;color:var(--ink)}
.what p{position:absolute;left:502px;top:106px;width:470px;font-size:14px;line-height:27px;color:var(--text)}
.btn-solid{position:absolute;background:var(--blue);color:var(--white);border-radius:23px;font-size:14px;font-weight:700;display:flex;align-items:center;justify-content:center}

/* Map */
.map{position:absolute;left:0;top:2128px;width:1200px;height:396px;background:linear-gradient(160deg,#ece9e3,#e3e4dd 50%,#eeebe4)}

/* Contact */
.contact{position:absolute;left:0;top:2524px;width:1200px;height:510px;background:linear-gradient(180deg,#3e4245,#5b5f61 40%,#474a4c)}
.contact .section-title{color:var(--white);top:64px}
.field{position:absolute;background:var(--white);font-size:13px;color:#444;padding:0 14px;display:flex;align-items:center}
.field.tall{align-items:flex-start;padding-top:12px}

/* Footer */
.footer-brand{position:absolute;left:97px;top:3155px;display:flex;align-items:center;gap:14px;font-size:30px;font-weight:500;color:#333}
.footer-brand .brand-mark{border-color:var(--blue);width:40px;height:40px}
.f-head{position:absolute;top:3100px;font-size:15px;font-weight:500;color:var(--ink)}
.f-links{position:absolute;left:414px;top:3139px;list-style:none;font-size:12px;line-height:25px;color:var(--text)}
.f-text{position:absolute;font-size:12px;line-height:20px;color:var(--text)}
.f-input{position:absolute;left:595px;top:3200px;width:255px;height:30px;border-bottom:1px solid var(--line);font-size:12px;color:#aaa;padding-top:8px}
.f-contact{position:absolute;left:915px;top:3150px;list-style:none;font-size:12px;color:var(--text)}
.f-contact li{display:flex;gap:14px;align-items:flex-start;line-height:18px;margin-bottom:16px}
.rule{position:absolute;left:97px;top:3312px;width:1006px;height:1px;background:#ddd}
.copy{position:absolute;left:97px;top:3344px;font-size:12px;color:var(--text)}
.social{position:absolute;top:3340px;display:flex;gap:8px;left:978px}
.social i{width:26px;height:26px;border-radius:50%;border:1px solid var(--blue)}
</style>
</head>
<body>

<header class="hero">
  <div class="hero-shade" role="img" aria-label="Photo of people working together at a table in a bright coworking space"></div>
  <div class="brand"><span class="brand-mark"></span>DeskHarbor</div>
  <nav class="nav">
    <span>Locations</span><span>Enterprise</span><span>Special promotions</span><span>Blog</span><span>Contact us</span><span>About us</span>
    <svg width="16" height="16" viewBox="0 0 16 16"><circle cx="6.5" cy="6.5" r="5" fill="none" stroke="#fff" stroke-width="2"/><line x1="10.3" y1="10.3" x2="15" y2="15" stroke="#fff" stroke-width="2.4"/></svg>
  </nav>
  <h1 class="hero-title">DeskHarbor Co-working</h1>
  <p class="hero-sub">DeskHarbor is a new global coworking brand</p>
  <div class="btn-ghost">GET MORE INFO</div>
  <div class="dots"><i></i><i></i><i></i><i></i></div>
  <svg class="abs" style="left:0;top:520px" width="1200" height="76" viewBox="0 0 1200 76">
    <polygon points="0,14 1200,64 1200,76 0,76" fill="#fff"/>
    <polygon points="0,14 1200,58 1200,66 0,76" fill="#2e9fd9"/>
  </svg>
</header>

<h2 class="section-title" style="top:666px">OUR VALUES</h2>
<p class="intro" style="top:726px">Coworking is a style of work that involves a shared working environment. Unlike in a typical office environment, those coworking are usually employed by various organizations.</p>

<svg class="chev" style="left:50px" width="16" height="28" viewBox="0 0 16 28"><polyline points="14,2 2,14 14,26" fill="none" stroke="#999" stroke-width="2.5"/></svg>
<svg class="chev" style="left:1132px" width="16" height="28" viewBox="0 0 16 28"><polyline points="2,2 14,14 2,26" fill="none" stroke="#999" stroke-width="2.5"/></svg>

<div class="value-card" style="left:97px">
  <div class="value-icon"><svg width="36" height="44" viewBox="0 0 36 44"><path d="M18 3a13 13 0 0 0-8 23c2 2 3 4 3 7h10c0-3 1-5 3-7A13 13 0 0 0 18 3z" fill="none" stroke="#777" stroke-width="2.5"/><line x1="13" y1="37" x2="23" y2="37" stroke="#777" stroke-width="2.5"/><line x1="15" y1="41" x2="21" y2="41" stroke="#777" stroke-width="2.5"/></svg></div>
  <h3>Inspire collaboration<br>&amp; Innovation</h3>
  <p>Coworking is not only about the physical place, but about</p>
  <span class="more">READ MORE</span>
</div>
<div class="value-card active" style="left:355px">
  <div class="value-icon"><svg width="48" height="40" viewBox="0 0 48 40"><circle cx="24" cy="10" r="7" fill="#2e9fd9"/><circle cx="10" cy="14" r="5.5" fill="#2e9fd9"/><circle cx="38" cy="14" r="5.5" fill="#2e9fd9"/><path d="M12 38c0-10 5-16 12-16s12 6 12 16z" fill="#2e9fd9"/><path d="M1 36c0-8 4-13 9-13 2 0 3 .5 4 1.5-2 3-3 7-3 11.5z" fill="#2e9fd9"/><path d="M47 36c0-8-4-13-9-13-2 0-3 .5-4 1.5 2 3 3 7 3 11.5z" fill="#2e9fd9"/></svg></div>
  <h3>Be a part of an<br>exclusive club</h3>
  <p>Coworking is not only about the physical place, but about</p>
  <span class="more">READ MORE</span>
</div>
<div class="value-card" style="left:611px">
  <div class="value-icon"><svg width="40" height="40" viewBox="0 0 40 40"><circle cx="20" cy="20" r="17" fill="none" stroke="#777" stroke-width="2.5"/><circle cx="14" cy="16" r="2" fill="#777"/><circle cx="26" cy="16" r="2" fill="#777"/><path d="M12 24q8 8 16 0" fill="none" stroke="#777" stroke-width="2.5"/></svg></div>
  <h3>Realize your<br>greatness</h3>
  <p>Coworking is not only about the physical place, but about</p>
  <span class="more">READ MORE</span>
</div>
<div class="value-card" style="left:867px">
  <div class="value-icon"><svg width="42" height="40" viewBox="0 0 42 40"><path d="M30 20v15H4V9h16" fill="none" stroke="#777" stroke-width="2.5"/><path d="M34 3l5 5-17 17-7 2 2-7z" fill="none" stroke="#777" stroke-width="2.5"/></svg></div>
  <h3>Style and design<br>awareness</h3>
  <p>Coworking is not only about the physical place, but about</p>
  <span class="more">READ MORE</span>
</div>

<section class="testimonials" role="img" aria-label="Blue-tinted photo of an open office behind customer testimonials">
  <h2 class="section-title">CUSTOMER TESTIMONIALS</h2>
  <div class="arrow-round" style="left:32px"><svg width="10" height="14" viewBox="0 0 10 14"><polyline points="8,1 2,7 8,13" fill="none" stroke="#fff" stroke-width="2"/></svg></div>
  <div class="arrow-round" style="left:1136px"><svg width="10" height="14" viewBox="0 0 10 14"><polyline points="2,1 8,7 2,13" fill="none" stroke="#fff" stroke-width="2"/></svg></div>

  <div class="quote" style="left:97px">
    <div class="avatar" role="img" aria-label="Customer portrait"></div>
    <p class="quote-body" style="left:91px"><b>“</b>We had sewerage overflowing out of the floor drain in our bathroom, we were not sure what to do so we called harbourside drain care...</p>
    <span class="quote-name" style="left:91px">Marla Quennell - Brookmere</span>
    <span class="quote-role" style="left:91px">Financial Services Professional</span>
    <div class="stars" style="left:91px">
      <svg width="96" height="18" viewBox="0 0 96 18"><g fill="#f2b500"><path id="s" d="M9 1l2.4 5.3 5.6.6-4.2 3.8 1.2 5.6L9 13.4 4 16.3l1.2-5.6L1 6.9l5.6-.6z"/><use href="#s" x="19"/><use href="#s" x="38"/><use href="#s" x="57"/></g><use href="#s" x="76" fill="none" stroke="#f2b500" stroke-width="1.3"/></svg>
    </div>
  </div>

  <div class="quote" style="left:446px">
    <div class="avatar" role="img" aria-label="Customer portrait"></div>
    <p class="quote-body" style="left:91px"><b>“</b>My apartments kitchen sink blocked up to the point where I couldn't use it at all. Desmond was very quick to come out and unblock it.</p>
    <span class="quote-name" style="left:91px">Tobin Arkwell - East Halden</span>
    <span class="quote-role" style="left:91px">Civic Futures Fellow at the Riverton</span>
    <div class="stars" style="left:91px">
      <svg width="96" height="18" viewBox="0 0 96 18"><g fill="#f2b500"><use href="#s"/><use href="#s" x="19"/><use href="#s" x="38"/><use href="#s" x="57"/></g><use href="#s" x="76" fill="none" stroke="#f2b500" stroke-width="1.3"/><path d="M85 1v12.4L80 16.3l1.2-5.6L77 6.9l5.6-.6z" fill="#f2b500"/></svg>
    </div>
  </div>

  <div class="quote" style="left:792px">
    <div class="avatar" role="img" aria-label="Customer portrait"></div>
    <p class="quote-body" style="left:91px;width:220px"><b>“</b>At vero eos et accusamus et iusto odio dignissimos ducimus qui blanditiis praesentium voluptatum deleniti atque corrupti quos dolores.</p>
    <span class="quote-name" style="left:91px">Vera Lindqvist</span>
    <span class="quote-role" style="left:91px">Creative Strategist | Entrepreneur &amp; Upcoming</span>
    <div class="stars" style="left:91px">
      <svg width="96" height="18" viewBox="0 0 96 18"><g fill="#f2b500"><use href="#s"/><use href="#s" x="19"/><use href="#s" x="38"/><use href="#s" x="57"/></g><use href="#s" x="76" fill="none" stroke="#f2b500" stroke-width="1.3"/></svg>
    </div>
  </div>
</section>

<section class="what">
  <div class="what-media" role="img" aria-label="Video still of a team meeting around a table in a loft office">
    <div class="play"><svg width="20" height="22" viewBox="0 0 20 22"><polygon points="3,1 19,11 3,21" fill="#fff"/></svg></div>
  </div>
  <h2>WHAT WE DO</h2>
  <p>Coworking is a style of work that involves a shared working environment. Unlike in a typical office environment, those coworking are usually employed by various organizations. Coworking is a gathering of a group of people who are working independently, but who share values, &amp; who are interested in the synergy that can happen from working with like-minded people.</p>
  <div class="btn-solid" style="left:502px;top:300px;width:138px;height:43px">READ MORE</div>
</section>

<section class="map" role="img" aria-label="Road map of the central United States showing location markers">
  <svg width="1200" height="396" viewBox="0 0 1200 396">
    <defs>
      <g id="pin"><circle r="27" fill="#2e9fd9" opacity=".35"/><circle r="19" fill="#2e9fd9"/><path d="M0-10a7 7 0 0 0-7 7c0 6 7 13 7 13s7-7 7-13a7 7 0 0 0-7-7z" fill="#fff"/><circle cy="-3" r="2.6" fill="#2e9fd9"/></g>
    </defs>
    <use href="#pin" x="183" y="102"/><use href="#pin" x="346" y="68"/><use href="#pin" x="220" y="226"/>
    <use href="#pin" x="374" y="272"/><use href="#pin" x="489" y="260"/><use href="#pin" x="736" y="272"/>
    <use href="#pin" x="845" y="310"/><use href="#pin" x="926" y="118"/><use href="#pin" x="1023" y="183"/>
  </svg>
</section>

<section class="contact" role="img" aria-label="Dimmed photo of an empty modern office interior">
  <h2 class="section-title">CONTACT US</h2>
  <div class="field" style="left:260px;top:141px;width:333px;height:41px">Your Name</div>
  <div class="field" style="left:607px;top:141px;width:333px;height:41px">Phone Number</div>
  <div class="field" style="left:260px;top:195px;width:333px;height:41px">Email Address</div>
  <div class="field" style="left:607px;top:195px;width:333px;height:41px">Address</div>
  <div class="field tall" style="left:260px;top:249px;width:680px;height:80px">Message</div>
  <div class="btn-solid" style="left:537px;top:349px;width:126px;height:45px;font-size:16px">SUBMIT</div>
  <svg class="abs" style="left:0;top:440px" width="1200" height="70" viewBox="0 0 1200 70">
    <polygon points="0,50 1200,10 1200,70 0,70" fill="#fff"/>
    <polygon points="0,50 1200,4 1200,16 0,60" fill="#2e9fd9"/>
  </svg>
</section>

<footer>
  <div class="footer-brand"><span class="brand-mark"></span>DeskHarbor</div>

  <h4 class="f-head" style="left:414px">QUICK LINKS</h4>
  <ul class="f-links"><li>Help</li><li>FAQ</li><li>Support</li><li>Sitemap</li><li>Terms Of Use</li><li>Privacy Statement</li></ul>

  <h4 class="f-head" style="left:595px">NEWSLETTER SUBSCRIPTION</h4>
  <p class="f-text" style="left:595px;top:3142px;width:240px">Register your Email Address to get Information about us</p>
  <div class="f-input">Email Address</div>
  <div class="btn-solid" style="left:595px;top:3250px;width:106px;height:30px;font-size:11px">SUBSCRIBE</div>

  <h4 class="f-head" style="left:915px">CONTACT US</h4>
  <ul class="f-contact">
    <li><svg width="12" height="16" viewBox="0 0 12 16"><path d="M6 0a6 6 0 0 0-6 6c0 5 6 10 6 10s6-5 6-10a6 6 0 0 0-6-6z" fill="#2e9fd9"/><circle cx="6" cy="6" r="2.2" fill="#fff"/></svg><span>Level 12, 48 Harrow Lane<br>Kestwick, UK</span></li>
    <li><svg width="14" height="14" viewBox="0 0 14 14"><path d="M3 0l3 3-2 2c1 2 3 4 5 5l2-2 3 3-2 3C6 14 0 8 0 3z" fill="#2e9fd9"/></svg><span>1-555-014-0188</span></li>
    <li><svg width="14" height="14" viewBox="0 0 14 14"><rect x="0" y="4" width="14" height="9" rx="1" fill="#2e9fd9"/><rect x="3" y="0" width="8" height="5" fill="#2e9fd9"/><rect x="3" y="7" width="8" height="3" fill="#fff"/></svg><span>1-555-014-0122</span></li>
    <li><svg width="14" height="12" viewBox="0 0 14 12"><rect width="14" height="11" rx="1" fill="#2e9fd9"/><polyline points="1,1 7,6 13,1" fill="none" stroke="#fff" stroke-width="1.4"/></svg><span>info@deskharbor.com</span></li>
  </ul>

  <div class="rule"></div>
  <p class="copy">Copyrights © 2017, DeskHarbor. All rights reserved.</p>
  <div class="social"><i></i><i></i><i></i><i></i></div>
</footer>

</body>
</html>
```